Business Card for Fashion House

We need a business card design for our personalize fashion service for our customers. the business card should reflect reliability, luxury and creativity.
The brand Gravetto is extracted from "Graceful Velvetto"; Gravetto provides fashion designs sprinkled with luxury and style tailored for our elite clients character profile.
Gravetto is created for those who embody class and elegance with a passion for style.
Target Market(s)
Affluent Customers
Industry/Entity Type
Fashion
Contact Information for Business Card
Samira Haddadin
Fashion Designer
Telephone: +971 4 555 0192
Mobile +971 50 555 0147
Emal info@gravetto-example.com
Website www.gravetto-example.com
Social Media Youtube g+ Facebook Instagram Pin /gravetto
Font styles to use
Other font styles liked:
- Audrey provided
Look and feel
Each slider illustrates characteristics of the customer's brand and the style your logo design should communicate.

```html
<!DOCTYPE html>
<html lang="en">
<head>
<meta charset="utf-8">
<title>Gravetto – Business Card</title>
<link rel="stylesheet" href="https://fonts.googleapis.com/css2?family=Marcellus&family=Roboto:wght@400&display=swap">
<style>
  :root {
    --backdrop: #3b3b3d;
    --card: #1c1c1e;
    --card-edge: #111112;
    --silver: #c9c9cc;
    --silver-dim: #8d8d92;
    --ink: #f2f2f2;
    --ink-soft: #cfcfd2;
  }
  * { box-sizing: border-box; margin: 0; padding: 0; }
  html, body {
    width: 799px; height: 1200px; overflow: hidden;
    background: var(--backdrop);
  }
  .canvas {
    position: relative; width: 799px; height: 1200px;
    display: flex; flex-direction: column; align-items: center;
    justify-content: space-around; padding: 60px 0;
  }
  .card {
    position: relative; width: 620px; height: 354px;
    background: var(--card);
    border: 1px solid var(--card-edge);
    box-shadow: 0 14px 30px rgba(0,0,0,.45);
    color: var(--ink);
  }

  /* Front */
  .card-front {
    display: flex; align-items: center; justify-content: center;
  }
  .brand-wordmark {
    font-family: "Marcellus", serif;
    font-size: 46px; letter-spacing: 16px;
    color: var(--silver); padding-left: 16px;
  }

  /* Back */
  .holder {
    position: absolute; top: 44px; left: 0; right: 0;
    text-align: center; padding-left: 90px;
  }
  .holder-name {
    font-family: "Marcellus", serif; font-size: 30px; color: var(--ink);
  }
  .holder-role {
    font-family: "Roboto", sans-serif; font-size: 13px;
    color: var(--ink-soft); margin-top: 4px; letter-spacing: .5px;
  }
  .contact-icons {
    display: flex; justify-content: center; gap: 10px; margin-top: 16px;
  }
  .contact-icons svg { width: 16px; height: 16px; }
  .contact-list {
    list-style: none; margin-top: 8px;
    font-family: "Roboto", sans-serif; font-size: 17px; line-height: 22px;
    color: var(--ink);
  }
  .divider {
    position: absolute; left: 28px; right: 28px; top: 262px; height: 1px;
    background: linear-gradient(90deg, var(--silver-dim), var(--silver), var(--silver-dim));
  }
  .social {
    position: absolute; top: 286px; left: 0; right: 0;
    display: flex; align-items: center; justify-content: center; gap: 10px;
    font-family: "Roboto", sans-serif; font-size: 19px; color: var(--ink);
  }
  .social-dot {
    width: 14px; height: 14px; border-radius: 50%; background: var(--silver);
  }
</style>
</head>
<body>
<main class="canvas">

  <section class="card card-front" aria-label="Card front">
    <h1 class="brand-wordmark">GRAVETTO</h1>
  </section>

  <section class="card card-back" aria-label="Card back">
    <div class="holder">
      <h2 class="holder-name">Samira Haddadin</h2>
      <p class="holder-role">Fashion Designer</p>

      <div class="contact-icons" aria-hidden="true">
        <svg viewBox="0 0 16 16" fill="none" stroke="#f2f2f2" stroke-width="1.3">
          <circle cx="8" cy="8" r="7"/>
          <path d="M5.5 4.5l1.3 1.6-.8 1a5 5 0 002.9 2.9l1-.8 1.6 1.3-.8 1.1c-3 .3-6.5-3.2-6.2-6.2z"/>
        </svg>
        <svg viewBox="0 0 16 16" fill="none" stroke="#f2f2f2" stroke-width="1.3">
          <rect x="4.5" y="1.5" width="7" height="13" rx="1.2"/>
          <line x1="7" y1="12.5" x2="9" y2="12.5"/>
        </svg>
        <svg viewBox="0 0 16 16" fill="none" stroke="#f2f2f2" stroke-width="1.3">
          <rect x="1.5" y="3.5" width="13" height="9"/>
          <path d="M1.5 3.5L8 9l6.5-5.5"/>
        </svg>
        <svg viewBox="0 0 16 16" fill="none" stroke="#f2f2f2" stroke-width="1.2">
          <circle cx="8" cy="8" r="6.5"/>
          <ellipse cx="8" cy="8" rx="3" ry="6.5"/>
          <line x1="1.5" y1="8" x2="14.5" y2="8"/>
        </svg>
      </div>

      <ul class="contact-list">
        <li>+971 4 555 0192</li>
        <li>+971 50 555 0147</li>
        <li>info@gravetto-example.com</li>
        <li>www.gravetto-example.com</li>
      </ul>
    </div>

    <div class="divider"></div>

    <p class="social"><span class="social-dot" aria-hidden="true"></span>/gravetto</p>
  </section>

</main>
</body>
</html>
```